4D Cradle Glimpse Luxury Ultrasound Billboard

Design a HIGH-END, MODERN billboard for my private prenatal ultrasound studio, 4D Cradle Glimpse, located in Pace, Florida.
This billboard will be viewed by drivers traveling at highway speeds, so it must be extremely clean, simple, and readable within 6 seconds.
About My Business
4D Cradle Glimpse is a private prenatal ultrasound studio specializing in:
Highest technology 4D/HD Ultrasounds
Early Gender Determination
Pregnancy Confirmation
I have been serving families for nearly 10 years and is known for creating a memorable experience, not just an ultrasound appointment.
Design Style
I DO NOT want:
Flowers
Leaves
Swirls
Glitter
Hearts everywhere
Busy backgrounds
Generic maternity stock graphics
I DO want:
Modern
Luxury
Upscale
Clean
Professional
Eye-catching
Premium medical spa feel
Colors
Use colors from my logo:
LOGO Green ( or a deep green)
Black
White
Soft Gold accents
Images:
Incorporate my professional headshot in a clean, modern way, logo, and the ultrasound images
Text
Keep wording minimal.
Primary Headline ( OPEN TO IDEAS) :
EXAMPLES ( WOULD RATHER SOMETHING MORE CATCHY)
" ADVANCED IMAGING. UNFORGETTABLE MOMENTS"
"MEET YOUR BABY BEFORE BIRTH"
Under headline:
4D Ultrasound • Early Gender • Pregnancy Confirmation
Business Name:
4D Cradle Glimpse
Private Prenatal Ultrasound Studio
Phone Number:
850-471-5923
Important
This billboard must be readable in 5–6 seconds from a moving vehicle.
Less text is better.
The phone number and business name must be visible from a distance.
The design should feel like a premium brand that immediately tells expecting parents:
“This is where I go to see my baby.”
Files Provided
Official logo
Headshot
Ultrasound images
Don’t make this look like a medical office billboard.
Make it look like a luxury baby experience billboard. That’s what separates 4D Cradle Glimpse from hospitals, OB offices, and all the new studios popping up around you. The emotional connection is what gets moms to book. ❤️
Billboard Size - 10.6” x 36”

```html
<!DOCTYPE html>
<html lang="en">
<head>
<meta charset="utf-8">
<title>4D Cradle Glimpse Billboard</title>
<link href="https://fonts.googleapis.com/css2?family=Montserrat:wght@400;500;600;800;900&display=swap" rel="stylesheet">
<style>
  :root {
    --stage: #d9d9d9;
    --green: #022d1f;
    --black: #000000;
    --white: #ffffff;
    --gold: #d2a83e;
    --logo-green: #5f7268;
  }
  * { margin: 0; padding: 0; box-sizing: border-box; }
  html, body { width: 1200px; height: 450px; overflow: hidden; background: var(--stage); }
  body { position: relative; font-family: "Montserrat", sans-serif; }

  .billboard {
    position: absolute; left: 43px; top: 47px; width: 1115px; height: 348px;
    background: var(--white); border: 7px solid var(--green); overflow: hidden;
  }
  .brand {
    position: absolute; left: 18px; top: 20px; width: 228px;
  }
  .brand-name {
    font-weight: 800; font-size: 36px; line-height: 40px; color: var(--logo-green);
    letter-spacing: -0.5px;
  }
  .brand-line {
    display: block;
  }
  .brand-descriptor {
    margin-top: 10px;
    font-weight: 600; font-size: 10.5px; letter-spacing: 0.4px; color: var(--logo-green);
    white-space: nowrap;
  }
  .tagline {
    position: absolute; left: 259px; top: 33px;
    font-weight: 500; font-size: 21px; line-height: 26px; color: var(--gold); white-space: nowrap;
  }
  .phone {
    position: absolute; left: 257px; top: 60px;
    font-weight: 800; font-size: 53px; line-height: 1; color: var(--black);
    letter-spacing: -0.5px; white-space: nowrap;
  }
  .headline {
    position: absolute; left: 18px; top: 143px;
    font-weight: 900; font-size: 61px; line-height: 73px; letter-spacing: -0.5px;
    white-space: nowrap;
  }
  .headline-top { display: block; color: var(--black); }
  .headline-bottom { display: block; color: var(--green); }
  .services {
    position: absolute; left: 18px; top: 292px;
    font-weight: 500; font-size: 21px; line-height: 26px; color: var(--gold); white-space: nowrap;
  }
  .ultrasound-image {
    position: absolute; left: 728px; top: 0; width: 373px; height: 334px;
    background: radial-gradient(ellipse at 30% 55%, #c07a6c 0%, #8e4a40 45%, transparent 70%),
                radial-gradient(ellipse at 78% 55%, #c58474 0%, #934c42 45%, transparent 70%),
                linear-gradient(90deg, #7a3b33 0%, #2a0f0d 50%, #7a3b33 100%);
  }
  .gold-line {
    position: absolute; left: 723px; top: 0; width: 4px; height: 36px; background: var(--gold);
  }
  .headshot-arch {
    position: absolute; left: 633px; top: 31px; width: 180px; height: 320px; z-index: 2;
    border: 4px solid var(--gold); border-bottom: none; border-radius: 90px 90px 0 0;
    background: linear-gradient(180deg, #dcdcdc 0%, #cfcfcc 45%, #4e5d52 75%, #2f3d33 100%);
  }
</style>
</head>
<body>
  <div class="billboard">
    <div class="brand">
      <div class="brand-name">
        <span class="brand-line">4D Cradle</span>
        <span class="brand-line">Glimpse</span>
      </div>
      <div class="brand-descriptor">PRENATAL ULTRASOUND STUDIO</div>
    </div>
    <div class="tagline">Let’s See Your Babay Before Birth</div>
    <div class="phone">850-471-5923</div>
    <h1 class="headline">
      <span class="headline-top">MEET YOUR BABY</span>
      <span class="headline-bottom">BEFORE BIRTH</span>
    </h1>
    <div class="services">4D Ultrasound • Early Gender • Pregnancy Confirmation</div>
    <div class="ultrasound-image" role="img" aria-label="4D ultrasound image of twin babies face to face"></div>
    <div class="gold-line"></div>
    <div class="headshot-arch" role="img" aria-label="Professional headshot of the sonographer in green scrubs holding an ultrasound probe in her studio"></div>
  </div>
</body>
</html>
```